Law Offices business card

Hi there, I'll need business card for the Law Offices of Colin Matheny. The information must convey his strategic approach and quick resolution to complex business litigation needs. Please emphasize Civil Litigation, Corporate Law, Business Governance and Real Estate Law. Colin has over 25 years of experience in these fields.The card should be modern and edgy and the message should be clear. Please consult his current website for ideas.

```html
<!DOCTYPE html>
<html lang="en">
<head>
<meta charset="utf-8">
<title>Law Offices of Colin Matheny – Business Card</title>
<link href="https://fonts.googleapis.com/css2?family=Tinos:wght@400;700&family=Noto+Sans:wght@400&display=swap" rel="stylesheet">
<style>
  :root {
    --page: #e6e3de;
    --card-black: #050304;
    --card-grey: #b0aeaf;
    --ink: #111111;
    --paper: #ffffff;
  }
  * { margin: 0; padding: 0; box-sizing: border-box; }
  html, body { width: 1189px; height: 1200px; overflow: hidden; background: var(--page); }
  .canvas { position: relative; width: 1189px; height: 1200px; }

  .card { position: absolute; left: 140px; width: 918px; height: 523px; background: var(--card-black); }
  .card--front { top: 47px; }
  .card--back { top: 624px; }

  .front-panel { position: absolute; left: 19px; top: 18px; width: 879px; height: 484px; background: var(--card-grey); color: var(--ink); }

  .holder-name { position: absolute; left: 72px; top: 50px; font: 700 44px/1 "Tinos", serif; letter-spacing: 0.2px; }
  .holder-title { position: absolute; left: 72px; top: 104px; font: 400 26px/1 "Noto Sans", sans-serif; }
  .firm-name { position: absolute; left: 72px; top: 178px; font: 400 43px/1 "Tinos", serif; }

  .contact-list { position: absolute; left: 72px; top: 280px; list-style: none; }
  .contact-item { display: flex; align-items: center; height: 41.5px; font: 400 25px/1 "Noto Sans", sans-serif; letter-spacing: 0.5px; }
  .contact-icon { width: 23px; height: 23px; margin-right: 26px; flex: none; }

  .service-heading { position: absolute; left: 94px; top: 52px; font: 400 58px/1 "Tinos", serif; color: var(--paper); }
  .service-rule { position: absolute; left: 0; top: 129px; width: 100%; height: 2px; background: var(--paper); }
  .service-list { position: absolute; left: 96px; top: 233px; list-style: none; color: var(--paper); }
  .service-item { display: flex; align-items: center; height: 58px; font: 400 31px/1 "Noto Sans", sans-serif; letter-spacing: 0.5px; }
  .service-bullet { width: 22px; height: 22px; margin-right: 24px; flex: none; }
</style>
</head>
<body>
<main class="canvas">
  <section class="card card--front" aria-label="Card front">
    <div class="front-panel">
      <h1 class="holder-name">Colin Matheny</h1>
      <p class="holder-title">Attorney</p>
      <p class="firm-name">Law offices of Colin Matheny,P.A.</p>
      <ul class="contact-list">
        <li class="contact-item">
          <svg class="contact-icon" viewBox="0 0 24 24" aria-hidden="true"><rect width="24" height="24" fill="#050304"/><path d="M7 4c-1 1-2 2-1 6s4 8 7 10c2 1 3 0 4-1l-2-3-2 1c-2-1-4-5-4-7l2-1-1-4z" fill="#fff"/></svg>
          <span>555-014-2736</span>
        </li>
        <li class="contact-item">
          <svg class="contact-icon" viewBox="0 0 24 24" aria-hidden="true"><rect width="24" height="24" fill="#050304"/><rect x="7" y="4" width="10" height="16" rx="1" fill="#fff"/><rect x="9" y="6" width="6" height="5" fill="#050304"/><rect x="9" y="13" width="6" height="5" fill="#777"/></svg>
          <span>555-019-4821</span>
        </li>
        <li class="contact-item">
          <svg class="contact-icon" viewBox="0 0 24 24" aria-hidden="true"><rect width="24" height="24" fill="#050304"/><circle cx="12" cy="12" r="8" fill="#fff"/><path d="M8 8c2 0 3 1 3 3s-2 2-2 4l-1 2c-2-2-3-5 0-9zM14 6c2 1 4 3 3 6l-2-1-1-2z" fill="#050304"/></svg>
          <span>www.mathenylaw.com</span>
        </li>
        <li class="contact-item">
          <svg class="contact-icon" viewBox="0 0 24 24" aria-hidden="true"><rect width="24" height="24" fill="#050304"/><rect x="4" y="7" width="16" height="11" fill="#fff"/><path d="M4 7l8 6 8-6M4 18l6-5M20 18l-6-5" stroke="#050304" stroke-width="1.3" fill="none"/></svg>
          <span>colin@mathenylaw.com</span>
        </li>
      </ul>
    </div>
  </section>

  <section class="card card--back" aria-label="Card back">
    <h2 class="service-heading">Service</h2>
    <div class="service-rule"></div>
    <ul class="service-list">
      <li class="service-item"><svg class="service-bullet" viewBox="0 0 22 22" aria-hidden="true"><circle cx="11" cy="11" r="6" fill="none" stroke="#bbb" stroke-width="1"/><circle cx="11" cy="11" r="2.5" fill="#fff"/><path d="M11 1v6M11 15v6M1 11h6M15 11h6" stroke="#ddd" stroke-width="1"/></svg><span>Civil Litigation</span></li>
      <li class="service-item"><svg class="service-bullet" viewBox="0 0 22 22" aria-hidden="true"><circle cx="11" cy="11" r="6" fill="none" stroke="#bbb" stroke-width="1"/><circle cx="11" cy="11" r="2.5" fill="#fff"/><path d="M11 1v6M11 15v6M1 11h6M15 11h6" stroke="#ddd" stroke-width="1"/></svg><span>Corporate Law</span></li>
      <li class="service-item"><svg class="service-bullet" viewBox="0 0 22 22" aria-hidden="true"><circle cx="11" cy="11" r="6" fill="none" stroke="#bbb" stroke-width="1"/><circle cx="11" cy="11" r="2.5" fill="#fff"/><path d="M11 1v6M11 15v6M1 11h6M15 11h6" stroke="#ddd" stroke-width="1"/></svg><span>Real Estate Law</span></li>
      <li class="service-item"><svg class="service-bullet" viewBox="0 0 22 22" aria-hidden="true"><circle cx="11" cy="11" r="6" fill="none" stroke="#bbb" stroke-width="1"/><circle cx="11" cy="11" r="2.5" fill="#fff"/><path d="M11 1v6M11 15v6M1 11h6M15 11h6" stroke="#ddd" stroke-width="1"/></svg><span>Business Governance</span></li>
    </ul>
  </section>
</main>
</body>
</html>
```